Realtor branding business card

modern, simple and self branding. Broker office logo needs to be used but not emphasized. Looking to brand myself

Target Market(s)

buyers, sellers and investors

Industry/Entity Type

Realtor

Contact Information for Business Card

Sample of my current business card on file

Requirements
Must have
• my website - tobiasmerrowkl.com
• Realtor logo
• Fair housing logo
Nice to have
• Colors from office logo but not a must
Should not have
• Do not want headshot

```html
<!DOCTYPE html>
<html lang="en">
<head>
<meta charset="utf-8">
<title>Tobias Merrow – Business Card</title>
<link href="https://fonts.googleapis.com/css2?family=Montserrat:wght@400;500;700;800&display=swap" rel="stylesheet">
<style>
  :root {
    --backdrop: #2a2c2f;
    --card: #ffffff;
    --navy: #25226e;
    --red: #e0262b;
    --ink: #55575c;
    --badge: #c9cbd3;
  }
  * { box-sizing: border-box; margin: 0; padding: 0; }
  html, body { width: 1200px; height: 780px; overflow: hidden; }
  body {
    background: var(--backdrop);
    font-family: "Montserrat", Arial, sans-serif;
    display: flex;
    align-items: center;
    justify-content: center;
    gap: 40px;
  }
  .card {
    width: 540px;
    height: 309px;
    background: var(--card);
    position: relative;
    border-bottom: 6px solid var(--navy);
    overflow: hidden;
  }

  /* brokerage name, kept modest */
  .brand {
    display: flex;
    align-items: center;
    gap: 8px;
    color: var(--navy);
    font-weight: 700;
    font-size: 13px;
    line-height: 1.2;
  }
  .brand-mark { width: 10px; height: 10px; background: var(--red); flex: none; }

  /* front */
  .card-front .agent-block {
    position: absolute;
    left: 0; right: 0; top: 96px;
    text-align: center;
  }
  .card-front .agent-name { font-size: 30px; }
  .card-front .agent-role { font-size: 14px; margin: 4px 0 0; }
  .card-front .website {
    position: absolute;
    bottom: 34px; left: 0; right: 0;
    text-align: center;
    font-size: 14px;
    color: var(--ink);
  }
  .card-front .website .accent { color: var(--red); }

  /* shared agent type */
  .agent-name {
    color: var(--navy);
    font-weight: 800;
    font-size: 20px;
    letter-spacing: 0.5px;
  }
  .agent-role { color: var(--ink); font-size: 12px; margin: 2px 0 12px; }

  /* back */
  .card-back {
    display: flex;
    align-items: center;
    padding: 0 0 0 34px;
  }
  .back-left {
    width: 180px;
    flex: none;
    display: flex;
    flex-direction: column;
    gap: 22px;
  }
  .divider {
    width: 2px; height: 170px;
    background: var(--red);
    margin: 0 24px 0 12px;
    flex: none;
  }
  .contact-list { list-style: none; font-size: 13px; color: var(--ink); }
  .contact-list li { display: flex; align-items: center; gap: 8px; line-height: 20px; }
  .contact-list svg { width: 11px; height: 11px; flex: none; }
  .address { margin-top: 12px; font-size: 13px; color: var(--ink); line-height: 18px; }

  .badges { display: flex; gap: 10px; }
  .badge { width: 36px; height: 36px; background: var(--badge); }
  .badge-round { border-radius: 50%; }
</style>
</head>
<body>
  <section class="card card-front">
    <div class="agent-block">
      <h1 class="agent-name">TOBIAS MERROW</h1>
      <p class="agent-role">Realtor</p>
    </div>
    <p class="website">www.<span class="accent">tobiasmerrowkl</span>.com</p>
  </section>

  <section class="card card-back">
    <div class="back-left">
      <div class="brand">
        <span class="brand-mark"></span>
        <span class="brand-name">Brightkey Realty Group</span>
      </div>
      <div class="badges">
        <span class="badge" role="img" aria-label="Realtor association badge"></span>
        <span class="badge badge-round" role="img" aria-label="Fair housing badge"></span>
      </div>
    </div>
    <span class="divider"></span>
    <div class="details">
      <h2 class="agent-name">TOBIAS MERROW</h2>
      <p class="agent-role">Realtor</p>
      <ul class="contact-list">
        <li>
          <svg viewBox="0 0 12 12" fill="none" stroke="#25226e" stroke-width="1.3"><rect x="3" y="1" width="6" height="10" rx="1"/><line x1="5" y1="9" x2="7" y2="9"/></svg>
          407. 555. 0143
        </li>
        <li>
          <svg viewBox="0 0 12 12" fill="#25226e"><path d="M2.5 1 L4.5 1 L5.2 3.5 L4 4.6 C4.7 6 6 7.3 7.4 8 L8.5 6.8 L11 7.5 L11 9.5 C11 10.3 10.3 11 9.5 11 C5 11 1 7 1 2.5 C1 1.7 1.7 1 2.5 1 Z"/></svg>
          407. 555. 0190
        </li>
        <li>
          <svg viewBox="0 0 12 12" fill="none" stroke="#25226e" stroke-width="1.2"><rect x="1" y="2.5" width="10" height="7"/><polyline points="1,2.5 6,6.5 11,2.5"/></svg>
          info@tobiasmerrowkl.com
        </li>
        <li>
          <svg viewBox="0 0 12 12" fill="none" stroke="#25226e" stroke-width="1.1"><circle cx="6" cy="6" r="5"/><ellipse cx="6" cy="6" rx="2.2" ry="5"/><line x1="1" y1="6" x2="11" y2="6"/></svg>
          www.tobiasmerrowkl.com
        </li>
      </ul>
      <p class="address">480 Harbor Pine Lane<br>Lakeview Springs, FL 32799</p>
    </div>
  </section>
</body>
</html>
```